Timber Ridge Athletics Web Design

Need to completely update website - simple and clean look - informative
this will be our main source for booking appointments etc. needs to have baseball and softball content. we currently have a site - looking to update - we would like you to design and add to our current site.

Target Market(s)

ages 15-45, youth and parents for kids- softball and baseball players /fitness

Industry/Entity Type

baseball and softball indoor training facility

Coding

Coded - Design and coding required

Number of Pages Required

5+ page

Colors

Designer to choose colors to be used in the design.

Requirements
Must have
• our colors of business are green and black- we need you to completely set up the website for us
Nice to have
• out current webiste is www.timberridge482.example

```html
<!DOCTYPE html>
<html lang="en">
<head>
<meta charset="utf-8">
<title>Timber Ridge Athletics – Baseball and Softball</title>
<link rel="stylesheet" href="https://fonts.googleapis.com/css2?family=Poppins:wght@400;500;600;700&display=swap">
<style>
:root{
  --black:#000;
  --green:#3fe000;
  --green-band:#a2e294;
  --white:#fff;
  --off-white:#fcfafc;
  --light-grey:#f2f2f2;
  --text:#111;
  --muted:#444;
  --border:#e2e2e2;
}
*{box-sizing:border-box;margin:0;padding:0}
html,body{width:1200px;height:3771px;overflow:hidden}
body{position:relative;font-family:'Poppins',sans-serif;color:var(--text);background:var(--white)}
.abs{position:absolute}
.btn{display:inline-block;background:var(--green);color:#000;font-weight:500;border-radius:6px;text-align:center;text-decoration:none}

/* nav */
.site-nav{left:0;top:0;width:1200px;height:82px;background:var(--black)}
.brand{left:112px;top:19px;height:44px;display:flex;align-items:center;gap:8px;color:var(--white);font-weight:600;font-size:17px;letter-spacing:.3px;white-space:nowrap}
.brand-dot{width:44px;height:44px;border:3px solid var(--green);border-radius:50%;flex:none}
.nav-links{left:432px;top:27px;display:flex;align-items:center;gap:34px;font-size:18px;font-weight:500;color:var(--white);white-space:nowrap}

/* hero */
.hero{left:0;top:82px;width:1200px;height:596px;background:radial-gradient(ellipse at 60% 20%,#c9c2a4 0%,#6d6a55 30%,#3a3a30 60%,#2b3a22 100%)}
.hero-turf{left:0;top:430px;width:1200px;height:166px;background:linear-gradient(180deg,#4c6e34,#6b8a4a)}
.hero-text{left:0;top:104px;width:1200px;text-align:center;color:var(--white)}
.hero-welcome{font-size:25px;font-weight:500}
.hero-title{font-size:60px;font-weight:700;line-height:70px;margin-top:6px}
.hero-btn{left:444px;top:300px;width:295px;height:52px;line-height:52px;font-size:23px;font-weight:600;border-radius:8px}
.hero-arrow{top:262px;color:var(--white);font-size:22px}
.dots{display:flex;gap:16px}
.dot{width:9px;height:9px;border-radius:50%;background:rgba(255,255,255,.45)}
.dot.on{background:var(--white)}

/* about */
.about{left:0;top:678px;width:1200px;height:598px;background:var(--off-white)}
.about-photo{left:111px;top:86px;width:489px;height:431px;background:linear-gradient(135deg,#b55a4c,#c9b09a 45%,#8a6a4e)}
.about-copy{left:617px;top:130px;width:480px}
.about-copy h2{font-size:26px;font-weight:500;margin-bottom:18px}
.about-copy p{font-size:15.5px;line-height:25.7px;color:#222}
.about-btn{left:617px;top:414px;width:120px;height:42px;line-height:42px;font-size:15px}

/* pricing */
.pricing{left:0;top:1276px;width:1200px;height:829px;background:var(--light-grey)}
.section-title{width:1200px;left:0;text-align:center;font-size:27px;font-weight:500}
.price-card{top:168px;width:472px;height:578px;background:var(--off-white);border:1px solid var(--border);text-align:center}
.price-photo{height:314px;background:linear-gradient(135deg,#c2281e,#e8c9b6 50%,#7a8b55)}
.price-card h3{font-size:20px;font-weight:500;margin-top:22px;letter-spacing:.5px}
.price-card p{font-size:17px;line-height:26px;padding:0 30px;margin-top:12px}
.price-card .price{font-size:18px;margin-top:14px;padding:0}
.price-card .btn{width:154px;height:40px;line-height:40px;font-size:17px;margin-top:18px}
.slide-arrow{font-size:22px;color:#555}

/* services */
.services{left:0;top:2105px;width:1200px;height:448px;background:var(--green-band)}
.service-card{top:84px;width:237px;height:280px;background:var(--white);text-align:center;padding-top:30px}
.service-icon{width:74px;height:74px;border-radius:50%;background:var(--green);margin:0 auto;display:flex;align-items:center;justify-content:center}
.service-card h3{font-size:17.5px;font-weight:500;margin-top:16px;white-space:nowrap}
.service-card p{font-size:14px;line-height:22px;color:#333;margin-top:6px;padding:0 20px}
.service-card .btn{width:138px;height:36px;line-height:36px;font-size:15px;margin-top:14px}

/* gallery */
.gallery{left:0;top:2553px;width:1200px;height:872px;background:var(--white)}
.shot{position:absolute}
.g-dots{left:585px;top:826px;display:flex;gap:16px}
.g-dots span{width:11px;height:11px;border-radius:50%;background:#b6efa4}
.g-dots span.on{background:var(--green)}

/* footer */
.site-footer{left:0;top:3425px;width:1200px;height:346px;background:var(--black);color:var(--white)}
.footer-brand{left:112px;top:92px;font-size:20px;font-weight:600;letter-spacing:.3px;white-space:nowrap}
.contact-list{left:114px;top:152px;list-style:none;font-size:15.5px;font-weight:500}
.contact-list li{display:flex;align-items:center;gap:14px;height:36px;white-space:nowrap}
.footer-col{top:78px}
.footer-col h4{font-size:20px;font-weight:500;margin-bottom:20px}
.footer-col ul{list-style:none;font-size:16px;font-weight:500}
.footer-col li{height:34px;white-space:nowrap}
.email-field{width:244px;height:38px;background:var(--white);color:#777;font-size:14px;padding:9px 12px;margin-top:14px}
.subscribe{width:110px;height:36px;line-height:36px;font-size:14px;margin-top:16px;border-radius:4px}
.footer-rule{left:0;top:300px;width:1200px;height:1px;background:#333}
.copyright{left:112px;top:318px;font-size:12px}
.socials{left:536px;top:314px;display:flex;gap:22px}
.socials span{width:18px;height:18px;border-radius:50%;border:2px solid var(--white)}
</style>
</head>
<body>

<header class="abs site-nav">
  <div class="abs brand"><span class="brand-dot"></span>Timber Ridge Athletics</div>
  <nav class="abs nav-links"><span>Home</span><span>About Us</span><span>Our Facility</span><span>Lessons</span><span>Gallery</span><span>Contact</span>
    <svg width="20" height="20" viewBox="0 0 20 20" style="margin-left:2px"><circle cx="8" cy="8" r="6.5" fill="none" stroke="#fff" stroke-width="2"/><line x1="13" y1="13" x2="19" y2="19" stroke="#fff" stroke-width="2"/></svg>
  </nav>
</header>

<section class="abs hero" role="img" aria-label="Baseball batter swinging in a floodlit stadium with catcher and umpire behind the plate">
  <div class="abs hero-turf"></div>
  <div class="abs hero-text">
    <div class="hero-welcome">WELCOME TO</div>
    <div class="hero-title">TIMBER RIDGE<br>BASEBALL AND SOFTBALL</div>
  </div>
  <a class="abs btn hero-btn">Booking Appointment</a>
  <span class="abs hero-arrow" style="left:56px">‹</span>
  <span class="abs hero-arrow" style="left:1142px">›</span>
  <div class="abs dots" style="left:557px;top:553px"><span class="dot on"></span><span class="dot"></span><span class="dot"></span><span class="dot"></span></div>
</section>

<section class="abs about">
  <div class="abs about-photo" role="img" aria-label="Batter in red and white swinging with catcher crouched behind"></div>
  <div class="abs about-copy">
    <h2>About Us</h2>
    <p>Timber Ridge Athletics is an elite baseball and softball training facility in Sacramento. We are committed to the development of these young athletes physically, mentally and emotionally on and off the field. We are here to train, guide and mentor the youth to become the best versions of themselves. Whether their sport takes them to the next level, Timber Ridge wants to see them thrive as human beings first above all else. " Don't be afraid to be great".</p>
  </div>
  <a class="abs btn about-btn">Read More</a>
</section>

<section class="abs pricing">
  <h2 class="abs section-title" style="top:76px">Team Rental Pricing</h2>
  <span class="abs slide-arrow" style="left:64px;top:400px">‹</span>
  <span class="abs slide-arrow" style="left:1118px;top:400px">›</span>
  <article class="abs price-card" style="left:111px">
    <div class="price-photo" role="img" aria-label="Baseball team in red jerseys celebrating with a trophy"></div>
    <h3>BASEBALL TEAM</h3>
    <p>Lorem Ipsum is simply dummy text of the printing and typesetting industry. Lorem Ipsum has been the industry's standard.</p>
    <p class="price">Rental Price : &nbsp;$ 350.00</p>
    <a class="btn">Learn More</a>
  </article>
  <article class="abs price-card" style="left:617px">
    <div class="price-photo" role="img" aria-label="Softball team in red jerseys cheering around a trophy"></div>
    <h3>SOFTBALL TEAM</h3>
    <p>Lorem Ipsum is simply dummy text of the printing and typesetting industry. Lorem Ipsum has been the industry's standard.</p>
    <p class="price">Rental Price : &nbsp;$ 300.00</p>
    <a class="btn">Learn More</a>
  </article>
</section>

<section class="abs services">
  <article class="abs service-card" style="left:111px">
    <div class="service-icon"><svg width="40" height="40" viewBox="0 0 40 40" fill="none" stroke="#000" stroke-width="1.6"><rect x="6" y="14" width="22" height="20"/><path d="M10 20h4M18 20h4M10 26h4M18 26h4"/><circle cx="30" cy="10" r="5"/></svg></div>
    <h3>Our Facility</h3><p>Lorem Ipsum has been the industry's standard.</p><a class="btn">Know More</a>
  </article>
  <article class="abs service-card" style="left:358px">
    <div class="service-icon"><svg width="40" height="40" viewBox="0 0 40 40" fill="none" stroke="#000" stroke-width="1.6"><rect x="9" y="6" width="20" height="28"/><path d="M13 13h12M13 19h12M13 25h8M32 8v24"/></svg></div>
    <h3>Lessons</h3><p>Lorem Ipsum has been the industry's standard.</p><a class="btn">Know More</a>
  </article>
  <article class="abs service-card" style="left:605px">
    <div class="service-icon"><svg width="40" height="40" viewBox="0 0 40 40" fill="none" stroke="#000" stroke-width="1.6"><circle cx="15" cy="11" r="5"/><path d="M6 34v-9a9 9 0 0 1 18 0v9"/><rect x="26" y="20" width="9" height="14"/></svg></div>
    <h3>Instructor Oppertunities</h3><p>Lorem Ipsum has been the industry's standard.</p><a class="btn">Know More</a>
  </article>
  <article class="abs service-card" style="left:851px">
    <div class="service-icon"><svg width="40" height="40" viewBox="0 0 40 40" fill="none" stroke="#000" stroke-width="1.6"><rect x="16" y="5" width="18" height="12"/><circle cx="9" cy="12" r="3"/><circle cx="10" cy="27" r="3"/><circle cx="20" cy="27" r="3"/><circle cx="30" cy="27" r="3"/><path d="M5 35a5 5 0 0 1 10 0M15 35a5 5 0 0 1 10 0M25 35a5 5 0 0 1 10 0"/></svg></div>
    <h3>Camps/Classes</h3><p>Lorem Ipsum has been the industry's standard.</p><a class="btn">Know More</a>
  </article>
  <div class="abs dots" style="left:571px;top:398px"><span class="dot on"></span><span class="dot"></span><span class="dot"></span></div>
</section>

<section class="abs gallery">
  <h2 class="abs section-title" style="top:74px;left:-6px">Gallery</h2>
  <div class="shot" role="img" aria-label="Batter swinging on a dirt infield with catcher behind" style="left:110px;top:137px;width:488px;height:390px;background:linear-gradient(135deg,#c9c6bd,#8f8576 55%,#5e5a52)"></div>
  <div class="shot" role="img" aria-label="Pitcher gripping a baseball in a stadium" style="left:617px;top:137px;width:472px;height:193px;background:linear-gradient(90deg,#3b3a36,#8d8a80 40%,#2f3a4a)"></div>
  <div class="shot" role="img" aria-label="Softball players in light blue uniforms on the field" style="left:617px;top:353px;width:472px;height:174px;background:linear-gradient(90deg,#6a8fb4,#b7c8d6 50%,#8a7a66)"></div>
  <div class="shot" role="img" aria-label="Softball team in navy uniforms huddled together" style="left:110px;top:550px;width:236px;height:242px;background:linear-gradient(135deg,#2c3550,#d8c46a 50%,#2a2f44)"></div>
  <div class="shot" role="img" aria-label="Runner sliding into base past a fielder" style="left:367px;top:550px;width:231px;height:242px;background:linear-gradient(135deg,#6b4b3c,#c9a78c 50%,#a04a3c)"></div>
  <div class="shot" role="img" aria-label="Fielder diving for a ball in a lit stadium" style="left:617px;top:548px;width:472px;height:241px;background:linear-gradient(180deg,#33475c,#5a6f80 45%,#6b4a30)"></div>
  <div class="abs g-dots"><span class="on"></span><span></span></div>
</section>

<footer class="abs site-footer">
  <div class="abs footer-brand">Timber Ridge Athletics</div>
  <ul class="abs contact-list">
    <li><svg width="14" height="18" viewBox="0 0 14 18"><path d="M7 0a7 7 0 0 0-7 7c0 5 7 11 7 11s7-6 7-11a7 7 0 0 0-7-7zm0 10a3 3 0 1 1 0-6 3 3 0 0 1 0 6z" fill="#fff"/></svg>1840, Alder Creek Ave , RA</li>
    <li><svg width="16" height="12" viewBox="0 0 16 12"><rect width="16" height="12" rx="1" fill="#fff"/><path d="M0 1l8 6 8-6" stroke="#000" stroke-width="1.4" fill="none"/></svg>info@timberridge.example</li>
    <li><svg width="14" height="16" viewBox="0 0 14 16"><path d="M3 0l3 4-2 2c1 2 3 4 5 5l2-2 3 3-2 3C6 15-1 7 1 1z" fill="#fff"/></svg>+1-555-014-2290</li>
  </ul>
  <div class="abs footer-col" style="left:388px"><h4>QUICK LINKS</h4><ul><li>About Us</li><li>Team Rental Pricing</li><li>Gallery</li><li>Contact Us</li></ul></div>
  <div class="abs footer-col" style="left:598px"><h4>MORE INFO</h4><ul><li>Our Facilities</li><li>Lessons</li><li>Instructor Oppertunities</li><li>Camps/Classes</li></ul></div>
  <div class="abs footer-col" style="left:847px"><h4>NEWSLETTER</h4>
    <div style="font-size:15.5px;font-weight:500;white-space:nowrap">Get latest updates and News.</div>
    <div class="email-field">Email Address</div>
    <a class="btn subscribe">SUBSCRIBE</a>
  </div>
  <div class="abs footer-rule"></div>
  <div class="abs copyright">© 2022 TimberRidgeAthletics</div>
  <div class="abs socials"><span></span><span></span><span></span><span></span></div>
</footer>

</body>
</html>
```